Graphic designs required for HR consulting Website

We need to items designed to be used on our website and in presentations.
Please view our website for design ideas.
http://www.brightmoor.com.au.42.vexaloft.pw
See attached Powerpoint doc for more info.
InfoGraphic 1
Needs to be turned into an infographic that will be embedded into the Brightmoor HR website.
The fonts should be Helvetica Neue and should have the look and feel of the website.
InfoGraphic 2
Needs to be turned into an infographic that will be embedded into the Brightmoor HR website and used in PPT and WORD proposals.
The fonts should be Helvetica Neue, the look and
feel should be consistent with the first infographic.
A mountain analogy is needed that shows how the sequence of services will come together to take businesses on the journey to becoming great.
2 versions of the same information are shown on the following slides. The first is for ease of visibility, the second is to show the sequence of services on the journey.
Samples of possible design ideas for inspiration are at bottom of ppt.
Consulting
- Helvetica

```html
<!DOCTYPE html>
<html lang="en">
<head>
<meta charset="utf-8">
<title>Brightmoor – People &amp; Performance Services</title>
<link rel="stylesheet" href="https://fonts.googleapis.com/css2?family=Inter:wght@300;400&display=swap">
<style>
  :root {
    --bg: #f8f6f2;
    --blue: #2690d3;
    --navy: #094168;
    --deep: #07375a;
    --white: #ffffff;
    --heading: #2a8fd4;
  }
  html, body { margin: 0; padding: 0; background: var(--bg); overflow: hidden; }
  .infographic {
    position: relative; width: 1200px; height: 847px; overflow: hidden;
    background: var(--bg);
    font-family: "Inter", "Helvetica Neue", Helvetica, Arial, sans-serif;
    font-weight: 300; color: var(--white);
  }
  .column-head {
    position: absolute; margin: 0; font-weight: 300; color: var(--heading);
    font-size: 32px; line-height: 40px; text-align: center; letter-spacing: -0.2px;
  }
  .column-head--needs { left: 146px; width: 440px; top: 24px; }
  .column-head--help { left: 657px; width: 440px; top: 42px; }

  .band-shadow {
    position: absolute; left: 216px; width: 768px; height: 30px;
    background: radial-gradient(ellipse at 50% 0%, rgba(0,0,0,0.22) 0%, rgba(0,0,0,0.08) 45%, rgba(0,0,0,0) 72%);
  }
  .band {
    position: absolute; height: 190px; overflow: hidden;
  }
  .band--compliance { left: 83px; top: 114px; width: 1042px; background: var(--blue); }
  .band--operations { left: 80px; top: 347px; width: 1048px; background: var(--navy); }
  .band--strategy { left: 79px; top: 570px; width: 1050px; background: var(--blue); }
  .band__chevron { position: absolute; left: 0; top: 0; width: 1042px; height: 190px; }

  .need-title, .service-title {
    position: absolute; margin: 0; font-weight: 300; font-size: 37px;
    line-height: 34px; letter-spacing: -0.6px; white-space: nowrap;
  }
  .need-text {
    position: absolute; margin: 0; font-size: 17.5px; line-height: 23.5px;
    white-space: nowrap;
  }
  .service-text {
    position: absolute; margin: 0; font-size: 19px; line-height: 28px; white-space: nowrap;
  }
</style>
</head>
<body>
<main class="infographic">
  <h2 class="column-head column-head--needs">The people &amp; performance<br>needs of every business</h2>
  <h2 class="column-head column-head--help">How we can help you</h2>

  <div class="band-shadow" style="top:304px"></div>
  <div class="band-shadow" style="top:538px"></div>
  <div class="band-shadow" style="top:760px"></div>

  <!-- Compliance -->
  <section class="band band--compliance">
    <svg class="band__chevron" viewBox="0 0 1302 238" preserveAspectRatio="none" aria-hidden="true">
      <polygon fill="var(--deep)" points="623,0 708,119 553,238 586,238 741,119 656,0"/>
      <polygon fill="var(--white)" points="656,0 741,119 586,238 663,238 818,119 733,0"/>
      <g fill="none" stroke="var(--blue)" stroke-width="3.5">
        <polyline points="702,0 787,119 632,238"/>
        <polyline points="710,0 795,119 640,238"/>
        <polyline points="718,0 803,119 648,238"/>
        <polyline points="726,0 811,119 656,238"/>
      </g>
    </svg>
    <h3 class="need-title" style="left:55px;top:24px">COMPLIANCE</h3>
    <p class="need-text" style="left:55px;top:66px">Trusted advice on people issues including<br>Fair Work Act compliance, redundancies,<br>performance management,<br>terminations, policies and safety.</p>
    <h3 class="service-title" style="left:665px;top:54px">HR ON-DEMAND</h3>
    <p class="service-text" style="left:667px;top:100px">Monthly subscription</p>
  </section>

  <!-- HR operations -->
  <section class="band band--operations">
    <svg class="band__chevron" viewBox="0 0 1302 238" preserveAspectRatio="none" aria-hidden="true">
      <polygon fill="var(--blue)" points="627,0 712,119 557,238 590,238 745,119 660,0"/>
      <polygon fill="var(--white)" points="660,0 745,119 590,238 667,238 822,119 737,0"/>
      <g fill="none" stroke="var(--navy)" stroke-width="3.5">
        <polyline points="706,0 791,119 636,238"/>
        <polyline points="714,0 799,119 644,238"/>
        <polyline points="722,0 807,119 652,238"/>
        <polyline points="730,0 815,119 660,238"/>
      </g>
    </svg>
    <h3 class="need-title" style="left:56px;top:31px">HR OPERATIONS</h3>
    <p class="need-text" style="left:58px;top:79px">Operational HR support including recruit-<br>ment, performance management and<br>training.</p>
    <h3 class="service-title" style="left:669px;top:27px">ONSITE OR REMOTE<br>HR MANAGER</h3>
    <p class="service-text" style="left:670px;top:109px">Outsourced HR (annual subscription)<br>OR adhoc HR support (fixed fee projects)</p>
  </section>

  <!-- People & performance strategy -->
  <section class="band band--strategy">
    <svg class="band__chevron" viewBox="0 0 1302 238" preserveAspectRatio="none" aria-hidden="true">
      <polygon fill="var(--navy)" points="628,0 713,119 558,238 591,238 746,119 661,0"/>
      <polygon fill="var(--white)" points="661,0 746,119 591,238 668,238 823,119 738,0"/>
      <g fill="none" stroke="var(--blue)" stroke-width="3.5">
        <polyline points="707,0 792,119 637,238"/>
        <polyline points="715,0 800,119 645,238"/>
        <polyline points="723,0 808,119 653,238"/>
        <polyline points="731,0 816,119 661,238"/>
      </g>
    </svg>
    <h3 class="need-title" style="left:58px;top:28px">PEOPLE &amp; PERFORMANCE<br>STRATEGY</h3>
    <p class="need-text" style="left:60px;top:112px">Business strategy and planning, strategic HR<br>frameworks and interventions to fuel your growth.</p>
    <h3 class="service-title" style="left:670px;top:35px">STRATEGIC<br>EXPERTISE</h3>
    <p class="service-text" style="left:671px;top:114px">Fixed fee project based expertise</p>
  </section>
</main>
</body>
</html>
```